Thornbury Building Company - Card Design

I am looking to use the logo designs that you already did for me to develop a business card. I would like the card to have a black background and be double sided. I want white and green logo and text. I have attached an inspiration photo of a look that I like. I would like to use the Vertical Logo attached to take up the full front side of the card. On the back where I have my name and information, I would like to have the horizontal logo or maybe even just the image of the 'A' and trees without the text. I am open, but I am looking for something clean and simple and I want the green to really pop! Additional files can be found under Design #: 58302946

Target Market(s)

Homeowners

Industry/Entity Type

Construction

Contact Information for Business Card

Name: Marcus Thornbury, Title: Project Manager, Phone: 555.274.8136, Email: thornburybuildingcompany@mailvesta.com, address: 487 Larkspur Ln, Marrowdale, CA 95033, Lic# 2468317

Colors
00AB8E
00BBA5
67D7C9
C6EFE9
E9F9F6

Requirements
Nice to have
• I would like to see the logos that I have already got from ArtLoomHub, though I am open to new ones

```html
<!DOCTYPE html>
<html lang="en">
<head>
<meta charset="utf-8">
<title>Thornbury Building Company – Business Card</title>
<link rel="stylesheet" href="https://fonts.googleapis.com/css2?family=Open+Sans:wght@400;600;700&display=swap">
<style>
  :root {
    --bg: #474747;
    --card-black: #161616;
    --brand-green: #72b845;
    --bright-green: #3bb84c;
    --deep-green: #2a8a3a;
    --white: #ffffff;
  }
  * { box-sizing: border-box; margin: 0; padding: 0; }
  html, body { width: 1200px; height: 801px; overflow: hidden; }
  body {
    background: var(--bg);
    font-family: "Open Sans", Arial, sans-serif;
    position: relative;
  }
  .card {
    position: absolute;
    top: 246px;
    width: 540px;
    height: 309px;
    border-radius: 3px;
    overflow: hidden;
    box-shadow: 0 12px 30px rgba(0,0,0,.35);
  }
  .card--front { left: 45px; background: var(--card-black); border-bottom: 2px solid var(--bright-green); }
  .card--back { left: 615px; background: var(--bright-green); }

  .brand {
    position: absolute;
    top: 34px;
    left: 200px;
    width: 280px;
    text-align: center;
    color: var(--white);
    font-weight: 700;
    font-size: 24px;
    line-height: 1.25;
  }
  .person {
    position: absolute;
    top: 116px;
    left: 40px;
  }
  .person__name { color: var(--brand-green); font-weight: 700; font-size: 21px; line-height: 1.2; }
  .person__title { color: var(--white); font-size: 13px; }
  .divider {
    position: absolute;
    top: 172px;
    left: 40px;
    width: 440px;
    height: 1.5px;
    background: var(--brand-green);
  }
  .contact {
    position: absolute;
    top: 186px;
    left: 40px;
    color: var(--white);
    font-size: 12px;
    line-height: 1.9;
  }
  .contact__row { display: flex; align-items: center; gap: 8px; }
  .contact__row svg { width: 13px; height: 13px; flex: none; }
  .address {
    position: absolute;
    top: 186px;
    right: 30px;
    color: var(--white);
    font-size: 12px;
    line-height: 1.9;
    text-align: right;
  }
  .band {
    position: absolute;
    left: 0; bottom: 0;
    width: 100%;
    height: 30px;
  }
  .emboss {
    position: absolute;
    left: 50%; top: 50%;
    width: 250px; height: 250px;
    transform: translate(-50%, -50%);
    border: 3px solid var(--deep-green);
    border-radius: 50%;
    display: flex;
    align-items: center;
    justify-content: center;
    text-align: center;
    color: var(--deep-green);
    font-weight: 700;
    font-size: 24px;
    line-height: 1.25;
    padding: 20px;
  }
</style>
</head>
<body>
  <section class="card card--front" aria-label="Business card, contact side">
    <div class="brand">Thornbury Building Company</div>

    <div class="person">
      <p class="person__name">Marcus Thornbury</p>
      <p class="person__title">Project Manager</p>
    </div>

    <div class="divider"></div>

    <div class="contact">
      <p class="contact__row">
        <svg viewBox="0 0 24 24" aria-hidden="true"><path fill="#72b845" d="M6.6 10.8a15 15 0 0 0 6.6 6.6l2.2-2.2c.3-.3.7-.4 1-.2 1.1.4 2.3.6 3.6.6.6 0 1 .4 1 1V20c0 .6-.4 1-1 1A17 17 0 0 1 3 4c0-.6.4-1 1-1h3.5c.6 0 1 .4 1 1 0 1.3.2 2.5.6 3.6.1.3 0 .7-.2 1z"/></svg>
        555.274.8136
      </p>
      <p class="contact__row">
        <svg viewBox="0 0 24 24" aria-hidden="true"><path d="M2 5h20v14H2z M2 5l10 8 10-8" fill="none" stroke="#72b845" stroke-width="2.5"/></svg>
        thornburybuildingcompany@mailvesta.com
      </p>
    </div>

    <div class="address">
      <p>487 Larkspur Ln, Marrowdale, CA 95033</p>
      <p>Lic # 2468317</p>
    </div>

    <svg class="band" viewBox="0 0 540 30" preserveAspectRatio="none" aria-hidden="true">
      <polygon points="0,0 340,0 330,30 0,30" fill="#72b845"/>
      <polygon points="346,0 540,0 540,30 336,30" fill="#ffffff"/>
    </svg>
  </section>

  <section class="card card--back" aria-label="Business card, brand side">
    <div class="emboss">Thornbury Building Company</div>
  </section>
</body>
</html>
```